Logo, Web and Mobile Designs for enterprise social media platform

All the details are in the attached document, please start reading the scope document first which explains what is this project about and the details about the needed deliverables, after that please read the UI_Requirements document which will detail what is expected regarding the coded web version since this is a coded contest, it is very important that you meet the UI requirements or suggest something else but we will need to agree first before working on the coded version

Good Luck

Target Market(s)

Enterprise Social Media

Industry/Entity Type

Media

Coding

Coded - Design and coding required

Number of Pages Required

5+ page

Font styles to use
Sans Serif

Requirements
Must have
• All the must haves are listed in the scope document so please check before you start

```html
<!DOCTYPE html>
<html lang="en">
<head>
<meta charset="utf-8">
<title>Teamora – Home</title>
<link rel="stylesheet" href="https://fonts.googleapis.com/css2?family=Oswald:wght@600;700&family=Roboto:wght@300;400;500&display=swap">
<style>
  :root {
    --bar-dark: #1b1b1b;
    --accent-orange: #f07a10;
    --accent-orange-dark: #e06400;
    --accent-blue: #4aa8e6;
    --accent-blue-dark: #3a90d0;
    --nav-muted: #9a9a9a;
    --white: #ffffff;
    --hero-sky: #8e9db0;
    --hero-mid: #5f7590;
    --hero-deep: #2f5a80;
    --dot-active: #2fc6d6;
  }
  * { box-sizing: border-box; margin: 0; padding: 0; }
  html, body { width: 1200px; height: 795px; overflow: hidden; background: var(--bar-dark); }
  body { position: relative; font-family: "Roboto", sans-serif; color: var(--white); }

  .site-header {
    position: absolute; left: 0; top: 0; width: 1200px; height: 123px;
    background: var(--bar-dark); border-top: 2px solid var(--accent-orange);
  }
  .brand {
    position: absolute; left: 85px; top: 14px; width: 150px;
    display: flex; flex-direction: column; align-items: center; gap: 10px;
  }
  .brand-mark { width: 50px; height: 50px; border-radius: 50%; background: var(--accent-orange); }
  .brand-name { font-family: "Roboto", sans-serif; font-weight: 400; font-size: 28px; letter-spacing: 1px; line-height: 1; color: var(--white); }

  .main-nav { position: absolute; left: 500px; top: 58px; display: flex; }
  .main-nav a {
    display: block; position: relative; font-size: 13px; font-weight: 500; letter-spacing: .6px;
    color: var(--nav-muted); text-decoration: none; margin-right: 45px;
  }
  .main-nav a.is-active { color: var(--white); }
  .main-nav a.is-active::after {
    content: ""; position: absolute; left: -3px; right: -3px; top: 20px; height: 4px; background: var(--accent-orange);
  }

  .auth-actions { position: absolute; left: 920px; top: 44px; display: flex; gap: 12px; }
  .btn {
    display: flex; align-items: center; justify-content: center; gap: 7px;
    width: 91px; height: 35px; border-radius: 2px; font-size: 13px; font-weight: 500; letter-spacing: .5px;
    color: var(--white); text-decoration: none;
  }
  .btn svg { width: 12px; height: 12px; fill: var(--white); }
  .btn-signup { background: linear-gradient(var(--accent-orange), var(--accent-orange-dark)); }
  .btn-login { background: linear-gradient(var(--accent-blue), var(--accent-blue-dark)); }

  .hero { position: absolute; left: 0; top: 123px; width: 1200px; height: 588px; overflow: hidden; }
  .hero-art {
    position: absolute; inset: 0;
    background:
      radial-gradient(ellipse 560px 260px at 600px 640px, #2a6494 0%, #3d6d95 55%, rgba(61,109,149,0) 100%),
      radial-gradient(ellipse 420px 300px at 600px 230px, #a3afbd 0%, rgba(163,175,189,0) 100%),
      linear-gradient(180deg, var(--hero-sky) 0%, var(--hero-mid) 60%, var(--hero-deep) 100%);
  }
  .hero-shade { position: absolute; inset: 0; background: rgba(20, 28, 40, .22); }
  .hero-title {
    position: absolute; left: 0; right: 0; top: 193px; text-align: center;
    font-family: "Oswald", sans-serif; font-weight: 700; font-size: 68px; line-height: 1; letter-spacing: 0;
    text-shadow: 0 3px 6px rgba(0,0,0,.45);
  }
  .hero-subtitle {
    position: absolute; left: 0; right: 0; top: 284px; text-align: center;
    font-weight: 300; font-size: 19px; letter-spacing: .3px;
  }
  .slider-dots { position: absolute; left: 566px; top: 556px; display: flex; gap: 4px; }
  .slider-dots span { width: 14px; height: 14px; border-radius: 50%; border: 2px solid var(--white); }
  .slider-dots span.is-active { border-color: var(--dot-active); }

  .site-footer { position: absolute; left: 0; top: 711px; width: 1200px; height: 84px; background: var(--bar-dark); }
  .copyright { position: absolute; left: 85px; top: 36px; font-size: 12px; font-weight: 300; color: #e6e6e6; }
  .social-links { position: absolute; left: 937px; top: 24px; display: flex; gap: 8px; }
  .social-links a {
    display: flex; align-items: center; justify-content: center;
    width: 38px; height: 38px; border-radius: 50%; border: 2px solid var(--white);
  }
  .social-links svg { width: 16px; height: 16px; fill: var(--white); }
</style>
</head>
<body>
  <header class="site-header">
    <div class="brand">
      <span class="brand-mark"></span>
      <span class="brand-name">TEAMORA</span>
    </div>
    <nav class="main-nav">
      <a href="#" class="is-active">HOME</a>
      <a href="#">ABOUT US</a>
      <a href="#">SERVICES</a>
      <a href="#">CONTACT US</a>
    </nav>
    <div class="auth-actions">
      <a href="#" class="btn btn-signup">
        <svg viewBox="0 0 12 12"><path d="M0 4.5h5V2l4 4-4 4V7.5H0z"/><path d="M7 0h5v12H7v-1.5h3.5v-9H7z"/></svg>
        SIGN UP
      </a>
      <a href="#" class="btn btn-login">
        <svg viewBox="0 0 12 12"><path d="M2 5h8v7H2z"/><path d="M3.5 5V3.5a2.5 2.5 0 0 1 5 0V5H7V3.5a1 1 0 0 0-2 0V5z"/></svg>
        LOGIN
      </a>
    </div>
  </header>

  <section class="hero">
    <div class="hero-art" role="img" aria-label="Illustration of many small people standing on a blue networked globe under light rays, with speech bubbles showing music, message, chat, search and media icons above them"></div>
    <div class="hero-shade"></div>
    <h1 class="hero-title">WELCOME TO TEAMORA</h1>
    <p class="hero-subtitle">Neque porro quisquam est qui dolorem ipsum quia dolor sit amet</p>
    <div class="slider-dots">
      <span></span><span class="is-active"></span><span></span><span></span>
    </div>
  </section>

  <footer class="site-footer">
    <p class="copyright">© Copy Rights 2015 Teamora.all Right Reserved.</p>
    <div class="social-links">
      <a href="#" aria-label="Chat">
        <svg viewBox="0 0 16 16"><path d="M2 2h12v9H7l-4 3v-3H2z"/></svg>
      </a>
      <a href="#" aria-label="Email">
        <svg viewBox="0 0 16 16"><path d="M1 3h14v10H1zM2.5 4.5v.4L8 8.6l5.5-3.7v-.4z" fill-rule="evenodd"/></svg>
      </a>
      <a href="#" aria-label="Phone">
        <svg viewBox="0 0 16 16"><path d="M4 1l3 3-1.5 2a8 8 0 0 0 4.5 4.5L12 9l3 3-2 3C7 15 1 9 1 3z"/></svg>
      </a>
      <a href="#" aria-label="Location">
        <svg viewBox="0 0 16 16"><path d="M8 1a5 5 0 0 1 5 5c0 4-5 9-5 9S3 10 3 6a5 5 0 0 1 5-5zm0 3a2 2 0 1 0 0 4 2 2 0 0 0 0-4z" fill-rule="evenodd"/></svg>
      </a>
    </div>
  </footer>
</body>
</html>
```